Clear Plastic Card Design

I am looking to have a business card designed from my logo icon. I am looking to match the style of a different business card I have attached in the files.
Looking for a card that is plastic, with layers of transparency in the shape of my logo icon (also attached in the files) - not a circle like the other card. The winning design will incorporate the red icon logo on the front and back and include the charity's name, "Light for the Weary Souls" in the same or similar font, as well as an email and phone number. For now, use the email: email@lightfortheweary-mail.org and the phone number 555-382-7194.
We like how the sample business card has transparency, partial and full opacity layers and a matching color scheme. Files will need to be in vector so that our business card printing company can work with it.
UPDATE:
We've some excellent designs in, thank you everyone! I got an early review from the owner, and he requested a minor redirect to find his perfect design. He wants the design to stand out by NOT being a rectangle. Try instead a circle, square, or best yet - something that falls in the outline of the logo icon, either fully or partially. Thank you, everyone!
Light for the Weary Souls text should be incorporated as well as a phone and email.

```html
<!DOCTYPE html>
<html lang="en">
<head>
<meta charset="utf-8">
<title>Light for the Weary Souls – Round Card</title>
<link rel="stylesheet" href="https://fonts.googleapis.com/css2?family=Roboto+Condensed:wght@700&family=Poppins:wght@400&display=swap">
<style>
  :root {
    --bg: #eeeeec;
    --card-red: #dc1a14;
    --card-red-soft: #ec6f6a;
    --card-white: #ffffff;
    --ink: #2b2b2b;
  }
  html, body {
    margin: 0;
    padding: 0;
    width: 1200px;
    height: 1200px;
    overflow: hidden;
    background: var(--bg);
  }
  .canvas {
    width: 1200px;
    height: 1200px;
    display: block;
  }
  .ring-text {
    font-family: "Roboto Condensed", "Arial Narrow", sans-serif;
    font-weight: 700;
    font-size: 54px;
    fill: var(--card-white);
    text-transform: uppercase;
  }
  .brand-name {
    font-family: "Poppins", "Helvetica", sans-serif;
    font-weight: 400;
    font-size: 46px;
    fill: var(--ink);
  }
</style>
</head>
<body>
<svg class="canvas" viewBox="0 0 1200 1200" xmlns="http://www.w3.org/2000/svg">
  <defs>
    <path id="path-clockwise" d="M600,950 a350,350 0 1,1 0,-700 a350,350 0 1,1 0,700"/>
    <path id="path-counter" d="M600,205 a395,395 0 1,0 0,790 a395,395 0 1,0 0,-790"/>
  </defs>

  <g class="card">
    <!-- clear base disc -->
    <circle class="card-base" cx="600" cy="600" r="500" fill="var(--card-white)" stroke="var(--card-red)" stroke-width="7"/>
    <!-- translucent layer -->
    <circle class="card-tint-layer" cx="585" cy="615" r="488" fill="var(--card-red-soft)" opacity="0.75"/>
    <circle class="card-clear-layer" cx="625" cy="585" r="478" fill="var(--card-white)" opacity="0.9"/>
    <!-- loose outline layers -->
    <circle class="card-outline" cx="610" cy="590" r="492" fill="none" stroke="var(--card-red)" stroke-width="4"/>
    <circle class="card-outline" cx="590" cy="612" r="470" fill="none" stroke="var(--card-red)" stroke-width="3"/>
    <circle class="card-outline" cx="620" cy="600" r="455" fill="none" stroke="var(--card-red)" stroke-width="3" opacity="0.8"/>

    <!-- red band -->
    <circle class="contact-band" cx="600" cy="600" r="370" fill="none" stroke="var(--card-red)" stroke-width="120"/>
    <circle class="band-edge" cx="600" cy="600" r="432" fill="none" stroke="var(--card-red)" stroke-width="5"/>

    <!-- centre disc -->
    <circle class="centre-disc" cx="600" cy="600" r="308" fill="var(--card-white)"/>
    <circle class="centre-ring" cx="600" cy="600" r="262" fill="none" stroke="var(--card-red)" stroke-width="10"/>

    <!-- curved contact text -->
    <text class="ring-text">
      <textPath href="#path-clockwise" startOffset="25%" text-anchor="middle">555-382-7194</textPath>
    </text>
    <text class="ring-text" font-size="50">
      <textPath href="#path-clockwise" startOffset="56%" text-anchor="middle">email@lightfortheweary-mail.org</textPath>
    </text>
    <text class="ring-text">
      <textPath href="#path-counter" startOffset="50%" text-anchor="middle">Light for the Weary Souls</textPath>
    </text>

    <!-- separator dots -->
    <circle class="separator" cx="355" cy="335" r="8" fill="var(--card-white)"/>
    <circle class="separator" cx="925" cy="790" r="8" fill="var(--card-white)"/>
    <circle class="separator" cx="278" cy="790" r="8" fill="var(--card-white)"/>

    <!-- charity name -->
    <circle class="brand-dot" cx="600" cy="500" r="38" fill="var(--card-red)"/>
    <text class="brand-name" x="600" y="615" text-anchor="middle">Light for the</text>
    <text class="brand-name" x="600" y="675" text-anchor="middle">Weary Souls</text>
  </g>
</svg>
</body>
</html>
```